business card for 3D Printing online platform for new company

Need a business card aligned to my logo attached.

back should be logo on full side. colour should be blue background.

front should convey the following info with orange text (bold/similar font to logo) and white background. logo should be on 1/3 coverage (on blue background) of front side with following details laid out on remainder 2/3 of side (white background):

"Making Imagination 3D..." - text should be hand written to look like it has been written with a fountain pen effect and in quotes.

The following "email", "call" and "web" below should be of 3D format, whether it be an icon or the text in 3D.

Colin Draper
Imagination Engineer

email :colin@lumvexprint.com
call: +44 (0) 77381 52907
web: www.lumvexprint.com

Thanks and good luck

Colin

thanks all for the submissions so far. there has been quite a few in a short space of time, but most have not addressed the brief that has been created. it must include the text as described and also I want some form of 3D design incorporated into the business card design.

thanks

colin

Business

Must have
• some form of 3D design whether it be the text (as requested above for the icons), or part of the card design.

```html
<!DOCTYPE html>
<html lang="en">
<head>
<meta charset="utf-8">
<title>Lumvex Business Card</title>
<link rel="stylesheet" href="https://fonts.googleapis.com/css2?family=Dancing+Script:wght@600&family=Open+Sans:wght@400;600;700;800&display=swap">
<style>
  :root {
    --page: #e6e7e9;
    --card: #ffffff;
    --blue: #1c86c8;
    --blue-deep: #0f5f99;
    --blue-light: #3aa0dd;
    --orange: #f0892a;
    --orange-side: #c9681a;
    --orange-dark: #a9540f;
    --ink: #2e3338;
    --ink-soft: #5a636d;
    --rule: #dde1e5;
  }
  * { box-sizing: border-box; margin: 0; padding: 0; }
  html, body {
    width: 1200px; height: 1005px; overflow: hidden;
    background: var(--page);
    font-family: "Open Sans", Arial, sans-serif;
    color: var(--ink);
  }
  .card {
    position: absolute; left: 190px; width: 820px; height: 469px;
    box-shadow: 0 6px 18px rgba(0,0,0,0.16);
    overflow: hidden;
  }

  /* Back: full blue with brand */
  .card--back {
    top: 22px;
    background: radial-gradient(ellipse at 50% 40%, var(--blue-light) 0%, var(--blue) 45%, var(--blue-deep) 100%);
  }
  .back-brand {
    position: absolute; left: 0; right: 0; top: 160px;
    display: flex; align-items: center; justify-content: center; gap: 24px;
  }
  .brand-dot { width: 104px; height: 104px; border-radius: 50%; background: #fff; flex: none; }
  .brand-name { font-weight: 700; font-size: 64px; line-height: 1; color: #fff; letter-spacing: 1px; }
  .back-url {
    position: absolute; left: 0; right: 0; top: 330px;
    text-align: center; font-size: 18px; color: #fff; letter-spacing: 0.5px;
  }

  /* Front */
  .card--front { top: 512px; background: var(--card); }
  .brand-panel {
    position: absolute; left: 0; top: 0; width: 273px; height: 469px;
    background: linear-gradient(160deg, var(--blue-light) 0%, var(--blue) 50%, var(--blue-deep) 100%);
    display: flex; flex-direction: column; align-items: center; justify-content: center; gap: 22px;
  }
  .brand-panel .brand-dot { width: 112px; height: 112px; }
  .brand-panel .brand-name { font-size: 46px; }

  .details { position: absolute; left: 273px; top: 0; width: 547px; height: 469px; padding: 44px 0 0 52px; }
  .holder-name {
    font-weight: 800; font-size: 34px; line-height: 40px;
    color: var(--orange); letter-spacing: 1px;
  }
  .holder-role {
    margin-top: 2px; font-weight: 700; font-size: 17px; line-height: 24px;
    color: var(--blue-deep); letter-spacing: 0.5px;
  }
  .tagline {
    margin-top: 16px;
    font-family: "Dancing Script", cursive; font-weight: 600;
    font-size: 34px; line-height: 42px; color: var(--blue-deep);
  }
  .details-rule { margin: 18px 52px 0 0; height: 1px; background: var(--rule); border: 0; }

  .contact { list-style: none; margin-top: 22px; }
  .contact li { display: flex; align-items: center; height: 50px; }
  .cube { width: 26px; height: 26px; flex: none; }
  .contact-label {
    width: 86px; margin-left: 14px;
    font-weight: 800; font-size: 21px; color: var(--orange);
    text-shadow: 1px 1px 0 var(--orange-side), 2px 2px 0 var(--orange-side), 3px 3px 0 var(--orange-dark), 4px 5px 6px rgba(0,0,0,0.25);
  }
  .contact-value { font-weight: 600; font-size: 18px; color: var(--orange); }

  .edge-band { position: absolute; left: 273px; right: 0; bottom: 0; height: 12px; background: var(--blue); }
</style>
</head>
<body>

<section class="card card--back" aria-label="Card back">
  <div class="back-brand">
    <span class="brand-dot"></span>
    <span class="brand-name">Lumvex</span>
  </div>
  <p class="back-url">www.lumvexprint.com</p>
</section>

<section class="card card--front" aria-label="Card front">
  <div class="brand-panel">
    <span class="brand-dot"></span>
    <span class="brand-name">Lumvex</span>
  </div>

  <div class="details">
    <h1 class="holder-name">Colin Draper</h1>
    <p class="holder-role">Imagination Engineer</p>
    <p class="tagline">“Making Imagination 3D...”</p>
    <hr class="details-rule">

    <ul class="contact">
      <li>
        <svg class="cube" viewBox="0 0 26 26" aria-hidden="true"><polygon points="13,2 24,8 13,14 2,8" fill="var(--orange)"/><polygon points="2,8 13,14 13,25 2,19" fill="var(--orange-side)"/><polygon points="24,8 13,14 13,25 24,19" fill="var(--orange-dark)"/></svg>
        <span class="contact-label">email</span>
        <span class="contact-value">colin@lumvexprint.com</span>
      </li>
      <li>
        <svg class="cube" viewBox="0 0 26 26" aria-hidden="true"><polygon points="13,2 24,8 13,14 2,8" fill="var(--orange)"/><polygon points="2,8 13,14 13,25 2,19" fill="var(--orange-side)"/><polygon points="24,8 13,14 13,25 24,19" fill="var(--orange-dark)"/></svg>
        <span class="contact-label">call</span>
        <span class="contact-value">+44 (0) 77381 52907</span>
      </li>
      <li>
        <svg class="cube" viewBox="0 0 26 26" aria-hidden="true"><polygon points="13,2 24,8 13,14 2,8" fill="var(--orange)"/><polygon points="2,8 13,14 13,25 2,19" fill="var(--orange-side)"/><polygon points="24,8 13,14 13,25 24,19" fill="var(--orange-dark)"/></svg>
        <span class="contact-label">web</span>
        <span class="contact-value">www.lumvexprint.com</span>
      </li>
    </ul>
  </div>

  <div class="edge-band"></div>
</section>

</body>
</html>
```